Marta's Dwellings website

We need a simple website for our property investment business in the UK. We basically need our contact details and brief description.We have the company logo already done (via ArtFlockly) so please use these:https://drive.google.com/drive/folders/1szJ3iRhelElZ40NIFT7w-c14MaY3Y_oV?usp=sharingYou could use some stock photos of UK houses for now.Let me know when to provide more detailed descriptions, etc

Coding

Coded - Design and coding required

Number of Pages Required

1 page

Colors

Designer to choose colors to be used in the design.

```html
<!DOCTYPE html>
<html lang="en">
<head>
<meta charset="utf-8">
<title>Marta's Dwellings</title>
<link href="https://fonts.googleapis.com/css2?family=Jost:wght@300;400&family=Roboto:wght@400;500;700&display=swap" rel="stylesheet">
<style>
:root{
  --blue:#1379d0;
  --blue-dark:#0f66b3;
  --ink:#222;
  --text:#666;
  --muted:#888;
  --dark:#161616;
  --dark-2:#262626;
  --light:#f3f4f7;
  --white:#fff;
}
*{box-sizing:border-box;margin:0;padding:0}
html,body{width:1200px;height:4018px;overflow:hidden}
body{position:relative;background:var(--white);font-family:Roboto,Arial,sans-serif;color:var(--text)}
.abs{position:absolute}
.heading{font-family:Jost,'Futura',sans-serif;font-weight:300;color:var(--ink);letter-spacing:1px;text-transform:uppercase}
.btn{position:absolute;background:var(--blue);color:#fff;font:700 17px Roboto,sans-serif;display:flex;align-items:center;justify-content:center;gap:7px;text-transform:uppercase}
.btn .arrow{width:15px;height:15px;border-radius:50%;background:#fff;position:relative}
.btn .arrow::after{content:"";position:absolute;left:4px;top:4px;border-left:6px solid var(--blue);border-top:3.5px solid transparent;border-bottom:3.5px solid transparent}

/* header */
.site-header{position:absolute;left:0;top:0;width:1200px;height:160px;background:#fff}
.brand{position:absolute;left:108px;top:38px;display:flex;flex-direction:column;align-items:center;gap:14px}
.brand-mark{width:64px;height:64px;background:var(--ink)}
.brand-name{font:400 14px Roboto,sans-serif;letter-spacing:6px;color:var(--ink);text-transform:uppercase}
.top-contact{position:absolute;right:111px;top:40px;font-size:15px;color:#444;display:flex;gap:26px;align-items:center}
.top-contact span{display:flex;align-items:center;gap:8px}
.main-nav{position:absolute;right:111px;top:98px;display:flex;gap:26px;font:500 16px Roboto,sans-serif;color:#222;align-items:center}

/* hero */
.hero{position:absolute;left:0;top:160px;width:1200px;height:620px;background:linear-gradient(180deg,#9db8cf 0%,#a76d55 35%,#8a4a36 60%,#6e7a4c 85%,#b9a893 100%)}
.hero-title{position:absolute;top:178px;width:100%;text-align:center;font:400 52px Jost,sans-serif;color:#fff;letter-spacing:1px}
.hero-sub{position:absolute;top:252px;width:100%;text-align:center;font:500 17px/26px Roboto,sans-serif;color:#fff}
.slider-arrow{position:absolute;top:289px;width:32px;height:32px;border-radius:50%;background:rgba(0,0,0,.35)}
.slider-arrow::after{content:"";position:absolute;top:12px;width:7px;height:7px;border-top:2px solid #fff;border-left:2px solid #fff}
.slider-arrow.prev{left:30px}.slider-arrow.prev::after{left:13px;transform:rotate(-45deg)}
.slider-arrow.next{right:30px}.slider-arrow.next::after{left:10px;transform:rotate(135deg)}

/* about */
.about{position:absolute;left:0;top:694px;width:1200px;height:800px;background:linear-gradient(180deg,#f5f5f5,#eceded)}
.about-title{position:absolute;left:111px;top:194px;font-size:48px}
.about-text{position:absolute;left:111px;top:284px;width:470px;font-size:14px;line-height:29px;color:var(--text)}
.about-text p+p{margin-top:29px}
.video-frame{position:absolute;left:627px;top:206px;width:461px;height:347px;background:#fff;padding:3px;box-shadow:0 2px 8px rgba(0,0,0,.15);z-index:2}
.video-still{width:100%;height:100%;background:linear-gradient(180deg,#6f9cc8 0%,#a9c3dc 35%,#a75a3c 55%,#7d3f2a 85%,#6d7a45 100%);position:relative}
.play{position:absolute;left:50%;top:50%;width:56px;height:56px;margin:-28px 0 0 -28px;background:rgba(0,0,0,.45);border:2px solid #fff;border-radius:50%}
.play::after{content:"";position:absolute;left:21px;top:16px;border-left:17px solid #fff;border-top:10px solid transparent;border-bottom:10px solid transparent}
.video-accent{position:absolute;left:1017px;top:484px;width:108px;height:106px;background:var(--blue)}

/* properties */
.properties-band{position:absolute;left:0;top:1386px;width:1200px;height:507px}
.properties-title{position:absolute;top:1536px;width:100%;text-align:center;font-size:46px;color:#fff}
.property-card{position:absolute;width:230px;height:293px;overflow:hidden;box-shadow:0 3px 10px rgba(0,0,0,.2)}
.property-card .photo{position:absolute;inset:0}
.property-card .info{position:absolute;left:0;bottom:0;width:100%;padding:0 24px 14px;background:linear-gradient(180deg,transparent,rgba(0,0,0,.6));color:#fff}
.property-card h3{font:700 21px Roboto,sans-serif;margin-bottom:8px}
.specs{display:flex;gap:16px;font-size:13px}
.specs span{display:flex;align-items:center;gap:4px}
.specs i{display:inline-block;width:13px;height:8px;background:#fff;border-radius:1px}

.divider{position:absolute;left:111px;top:2247px;width:977px;height:1px;background:#ddd}

/* projects */
.projects-title{position:absolute;top:2340px;width:100%;text-align:center;font-size:46px}
.projects-intro{position:absolute;left:220px;top:2416px;width:760px;text-align:center;font-size:14px;line-height:27px}
.project-tile{position:absolute;top:2564px;height:214px}
.project-feature{position:absolute;left:421px;top:2512px;width:359px;height:344px;background:#fff;box-shadow:0 2px 10px rgba(0,0,0,.18);padding:4px}
.project-feature .photo{height:249px}
.project-feature h3{position:absolute;left:16px;top:280px;font:500 21px Roboto,sans-serif;color:#333}
.project-feature p{position:absolute;left:16px;top:314px;font-size:13px;color:#444}
.project-feature .view{position:absolute;right:18px;top:290px;width:66px;height:30px;font-size:13px}
.project-feature .view .arrow{width:11px;height:11px}
.project-feature .view .arrow::after{left:3px;top:3px;border-left-width:5px;border-top-width:2.5px;border-bottom-width:2.5px}

/* news */
.news-title{position:absolute;top:2952px;width:100%;text-align:center;font-size:46px}
.news-card{position:absolute;top:3051px;width:302px}
.news-card .photo{height:187px;border:3px solid #fff;box-shadow:0 1px 6px rgba(0,0,0,.15);position:relative}
.date{position:absolute;left:16px;top:12px;width:44px;height:54px;background:var(--blue);color:#fff;text-align:center;font-size:11px;padding-top:7px}
.date b{display:block;font-size:20px;font-weight:700}
.news-card h3{margin-top:30px;font:400 19px/26px Roboto,sans-serif;color:#333}
.meta{margin-top:12px;font-size:13px;color:var(--muted);display:flex;gap:10px;align-items:center}
.meta i{display:inline-block;width:10px;height:10px;background:var(--blue);border-radius:50%}
.news-card p{margin-top:16px;font-size:14px;line-height:23px;color:var(--muted);text-align:justify}

/* footer */
.footer{position:absolute;left:0;top:3467px;width:1200px;height:551px}
.footer-heading{position:absolute;top:3626px;font:700 18px Roboto,sans-serif;color:#fff;text-transform:uppercase}
.footer-text{color:#ddd;font-size:13px;line-height:24px}
.field{position:absolute;height:40px;border:1px solid #666;color:#ddd;font-size:11px;padding:12px 14px}
.submit{position:absolute;left:332px;top:3796px;width:210px;height:40px;font-size:17px}
.quick-links{position:absolute;left:624px;top:3669px;list-style:none;font-size:13px;color:#ddd}
.quick-links li{height:30.4px;display:flex;align-items:center;gap:18px}
.quick-links li::before{content:"»";color:#ddd;font-size:14px}
.contact-row{position:absolute;left:810px;display:flex;gap:26px;align-items:flex-start}
.contact-row svg{flex:none;margin-top:4px}
.social{position:absolute;top:3883px;left:490px;display:flex;gap:8px}
.social span{width:37px;height:37px;border:2px solid #fff;border-radius:50%}
.footer-rule{position:absolute;top:3901px;height:1px;background:#666}
.copyright{position:absolute;top:3952px;width:100%;text-align:center;color:#fff;font-size:13px}
</style>
</head>
<body>

<header class="site-header">
  <div class="brand">
    <div class="brand-mark"></div>
    <div class="brand-name">Marta's Dwellings</div>
  </div>
  <div class="top-contact">
    <span><svg width="12" height="12" viewBox="0 0 12 12"><path d="M2 1l3 0 1 3-2 1a7 7 0 0 0 3 3l1-2 3 1 0 3c-6 0-9-3-9-9z" fill="#1379d0"/></svg>(+000) 555 010 2040</span>
    <span style="color:#999">|</span>
    <span><svg width="14" height="11" viewBox="0 0 14 11"><rect width="14" height="11" fill="#1379d0"/><path d="M0 0l7 6 7-6" stroke="#fff" fill="none"/></svg>info@martasdwellings-example.com</span>
  </div>
  <nav class="main-nav">
    <span>HOME</span><span>ABOUT US</span><span>SERVICES</span><span>PROJECTS</span><span>BLOG</span><span>CONTACT US</span>
    <svg width="16" height="16" viewBox="0 0 16 16"><circle cx="6.5" cy="6.5" r="5" stroke="#222" stroke-width="2" fill="none"/><path d="M10 10l5 5" stroke="#222" stroke-width="2.4"/></svg>
  </nav>
</header>

<section class="hero" role="img" aria-label="Photograph of a red brick house with conservatory, garden benches and hanging flower baskets">
  <div class="slider-arrow prev"></div>
  <div class="slider-arrow next"></div>
  <h1 class="hero-title">MARTA'S DWELLINGS</h1>
  <p class="hero-sub">Lorem ipsum dolor sit amet consectetur adipiscing elit sed do eiusmod<br>tempor incididunt ut labore et dolore magna aliqua.</p>
  <div class="btn" style="left:496px;top:340px;width:209px;height:46px">Get Started <span class="arrow"></span></div>
</section>

<section class="about">
  <h2 class="heading about-title">About Us</h2>
  <div class="about-text">
    <p>Lorem ipsum dolor sit amet, consectetur adipiscing elit, sed do eiusmod tempor incididunt ut labore et dolore magna aliqua.</p>
    <p>Ut enim ad minim veniam, quis nostrud exercitation ullamco laboris nisi ut aliquip ex ea commodo consequat. Duis aute irure dolor in reprehen derit in voluptate velit esse cillum dolore eu fugiat nulla pariatur. Excep teur sint occaecat cupidatat non proident...</p>
  </div>
  <div class="btn" style="left:111px;top:525px;width:182px;height:50px">Read More <span class="arrow"></span></div>
  <div class="video-accent"></div>
  <div class="video-frame">
    <div class="video-still" role="img" aria-label="Video still of a large red brick detached house under a blue sky">
      <div class="play"></div>
    </div>
  </div>
</section>

<svg class="abs" style="left:0;top:0" width="1200" height="780" viewBox="0 0 1200 780">
  <path d="M0 780 L0 772 Q300 720 600 688 Q900 720 1200 772 L1200 780 Z" fill="#1379d0"/>
  <path d="M0 780 Q300 730 600 700 Q900 730 1200 780 Z" fill="#f5f5f5"/>
</svg>

<svg class="abs properties-band" width="1200" height="507" viewBox="0 0 1200 507" role="img" aria-label="Darkened photograph of a row of brick houses">
  <defs><linearGradient id="bandShade" x1="0" y1="0" x2="0" y2="1"><stop offset="0" stop-color="#2a2624"/><stop offset="1" stop-color="#1b1b1b"/></linearGradient></defs>
  <path d="M0 92 L600 0 L1200 92 L1200 507 L0 507 Z" fill="url(#bandShade)"/>
</svg>
<div class="abs" style="left:0;top:1893px;width:1200px;height:1100px;background:linear-gradient(180deg,#f4f5f9,#f7f7f8)"></div>

<h2 class="heading properties-title">Our Properties</h2>

<article class="property-card" style="left:112px;top:1665px">
  <div class="photo" role="img" aria-label="Interior with an open wooden staircase and potted plants" style="background:linear-gradient(160deg,#e8e3dc,#b7a897 55%,#5a4030)"></div>
  <div class="info"><h3>Properity Name</h3><div class="specs"><span><i></i>05</span><span><i></i>08</span><span><i></i>02</span></div></div>
</article>
<article class="property-card" style="left:362px;top:1721px">
  <div class="photo" role="img" aria-label="Red brick detached house with bay windows" style="background:linear-gradient(180deg,#6f9dd0 0%,#9a4e36 40%,#7a3a28 75%,#5c6a40)"></div>
  <div class="info"><h3>Properity Name</h3><div class="specs"><span><i></i>05</span><span><i></i>08</span><span><i></i>02</span></div></div>
</article>
<article class="property-card" style="left:609px;top:1665px">
  <div class="photo" role="img" aria-label="Cosy living room with sofa and cushions" style="background:linear-gradient(160deg,#e6ddd2,#b58a66 50%,#6a3a26)"></div>
  <div class="info"><h3>Properity Name</h3><div class="specs"><span><i></i>05</span><span><i></i>08</span><span><i></i>02</span></div></div>
</article>
<article class="property-card" style="left:858px;top:1721px">
  <div class="photo" role="img" aria-label="Modern dining room with artwork on the wall" style="background:linear-gradient(160deg,#d8d6d3,#9e9a95 50%,#3e3a36)"></div>
  <div class="info"><h3>Properity Name</h3><div class="specs"><span><i></i>05</span><span><i></i>08</span><span><i></i>02</span></div></div>
</article>

<div class="btn" style="left:452px;top:2077px;width:296px;height:48px">View All Properties <span class="arrow"></span></div>

<div class="divider"></div>

<h2 class="heading projects-title">Our Projects</h2>
<p class="projects-intro">Lorem ipsum dolor sit amet, consectetur adipiscing elit, sed do eiusmod tempor incididunt ut labore et dolore magna aliqua. Ut enim ad minim veniam, quis nostrud exercitation ullamco laboris nisi ut aliquip.</p>

<div class="project-tile" style="left:0;width:208px;background:linear-gradient(180deg,#8fb0d0,#c08f63 45%,#b8453c 80%,#8a6d4e)" role="img" aria-label="Colourful terraced townhouses"></div>
<div class="project-tile" style="left:211px;width:207px;background:linear-gradient(180deg,#4f86c9,#b9b1a6 45%,#8c3c36 75%,#4a4a4a)" role="img" aria-label="Modern terraced houses with red and grey cladding"></div>
<div class="project-tile" style="left:781px;width:206px;background:linear-gradient(180deg,#4f86c9,#b49263 50%,#7c6a44 75%,#4f7d31)" role="img" aria-label="Row of new build brick houses behind a lawn"></div>
<div class="project-tile" style="left:990px;width:210px;background:linear-gradient(180deg,#5d8ec9,#b0613f 45%,#944a31 70%,#5a8a34)" role="img" aria-label="Red brick family homes with green garden"></div>

<article class="project-feature">
  <div class="photo" role="img" aria-label="Victorian brick houses along a tree-lined street" style="background:linear-gradient(180deg,#3e74c2 0%,#8eb1d6 35%,#a85f3e 60%,#7a4a35 85%,#6b6b5c)"></div>
  <h3>Project Name</h3>
  <p>Lorem ipsum dolor amet consectetur.</p>
  <div class="btn view">VIEW <span class="arrow"></span></div>
</article>

<h2 class="heading news-title">Latest News</h2>

<article class="news-card" style="left:111px">
  <div class="photo" role="img" aria-label="Red brick detached house with lawn" style="background:linear-gradient(180deg,#3b7ec9,#a9c7e3 35%,#9c4c34 60%,#62853a)"><div class="date">Apr<b>22</b></div></div>
  <h3>Minus id quod maxime placeat Facere possimus</h3>
  <div class="meta"><i></i>Dana <span>|</span><i></i>214 Comments</div>
  <p>Nam libero tempore, cum soluta nobis est eli gendi optio cumque nihil impedit.</p>
</article>
<article class="news-card" style="left:448px">
  <div class="photo" role="img" aria-label="Red brick detached house with lawn" style="background:linear-gradient(180deg,#3b7ec9,#a9c7e3 35%,#9c4c34 60%,#62853a)"><div class="date">Apr<b>05</b></div></div>
  <h3>Minus id quod maxime placeat Facere possimus</h3>
  <div class="meta"><i></i>Dana <span>|</span><i></i>214 Comments</div>
  <p>Nam libero tempore, cum soluta nobis est eli gendi optio cumque nihil impedit.</p>
</article>
<article class="news-card" style="left:785px">
  <div class="photo" role="img" aria-label="Terraced houses with autumn tree" style="background:linear-gradient(180deg,#dfe6ee,#7a7d86 40%,#c98a3d 60%,#55524d)"><div class="date">Apr<b>22</b></div></div>
  <h3>Minus id quod maxime placeat Facere possimus</h3>
  <div class="meta"><i></i>Dana <span>|</span><i></i>214 Comments</div>
  <p>Nam libero tempore, cum soluta nobis est eli gendi optio cumque nihil impedit.</p>
</article>

<svg class="abs footer" width="1200" height="551" viewBox="0 0 1200 551">
  <path d="M0 92 Q300 40 600 0 Q900 40 1200 92 L1200 100 L0 100 Z" fill="#1379d0"/>
  <path d="M0 100 Q300 54 600 16 Q900 54 1200 100 L1200 551 L0 551 Z" fill="#161616"/>
</svg>

<h4 class="footer-heading" style="left:111px">Inquire Form</h4>
<p class="abs footer-text" style="left:111px;top:3673px;width:440px">At vero eos et accusamus et iusto odio dignissimos ducimus qui blan-ditiis praesentium voluptatum deleniti...</p>
<div class="field" style="left:111px;top:3739px;width:209px">Name</div>
<div class="field" style="left:332px;top:3739px;width:210px">Email</div>
<div class="field" style="left:111px;top:3796px;width:209px">Phone No</div>
<div class="btn submit">Submit</div>

<h4 class="footer-heading" style="left:624px">Quick Links</h4>
<ul class="quick-links">
  <li>Home</li><li>About Us</li><li>Our Services</li><li>Projects</li><li>News</li><li>Contact Us</li>
</ul>

<h4 class="footer-heading" style="left:810px">Contact Details</h4>
<div class="contact-row footer-text" style="top:3672px">
  <svg width="14" height="18" viewBox="0 0 14 18"><path d="M7 17C3 11 1 8 1 6a6 6 0 0 1 12 0c0 2-2 5-6 11z" stroke="#aaa" fill="none"/><circle cx="7" cy="6" r="2" stroke="#aaa" fill="none"/></svg>
  <span style="width:240px">Suite 7, Orchard Court, 12-14 Willow Row, Brackenford, Northshire, United Kingdom, BF4 9QX</span>
</div>
<div class="contact-row footer-text" style="top:3765px">
  <svg width="16" height="16" viewBox="0 0 12 12"><path d="M2 1l3 0 1 3-2 1a7 7 0 0 0 3 3l1-2 3 1 0 3c-6 0-9-3-9-9z" stroke="#aaa" fill="none" stroke-width=".8"/></svg>
  <span>(+000) 555 0102 040</span>
</div>
<div class="contact-row footer-text" style="top:3814px">
  <svg width="16" height="12" viewBox="0 0 16 12"><rect x=".5" y=".5" width="15" height="11" stroke="#aaa" fill="none"/><path d="M1 1l7 6 7-6" stroke="#aaa" fill="none"/></svg>
  <span>info@martasdwellings-example.com</span>
</div>

<div class="footer-rule" style="left:111px;width:360px"></div>
<div class="footer-rule" style="left:730px;width:358px"></div>
<div class="social"><span></span><span></span><span></span><span></span><span></span></div>
<p class="copyright">Copyrights © 2019 Marta's Dwellings.&nbsp; All Rights Reserved &nbsp;&nbsp;|&nbsp;&nbsp; Privacy Policy.</p>

</body>
</html>
```